Harborline Claims Advocates Business card

We need to get business card Design for our Company we are Public Adjusters in Chicago Illinois - i like to see good combination and elements from my Company Logo. as well To be an two side design
Updates

Target Market(s)

Home /Business owner Property Managers

Industry/Entity Type

Business

Contact Information for Business Card

to show the Element of our logo i will Like 3D

Font styles to use
Sans Serif

Requirements
Must have
• Logo and Element of the Logo in 3D
Nice to have
• Logo That we Provide 3D Same Colors or open for suggestions
Should not have
• unleare view -

```html
<!DOCTYPE html>
<html lang="en">
<head>
<meta charset="UTF-8">
<title>Harborline Claims Advocates — Business Card</title>
<link href="https://fonts.googleapis.com/css2?family=Open+Sans:wght@400;600;700&display=swap" rel="stylesheet">
<style>
  :root {
    --page-bg: #ece9e4;
    --brand-red: #cc0a0a;
    --brand-blue: #0b3fd0;
    --brand-navy: #0a0f45;
    --paper: #ffffff;
    --ink-light: #ffffff;
    --wordmark-blue: #1d4fc4;
  }
  html, body {
    margin: 0;
    padding: 0;
    width: 1200px;
    height: 987px;
    overflow: hidden;
    background: var(--page-bg);
    font-family: "Open Sans", sans-serif;
  }
  .canvas {
    position: relative;
    width: 1200px;
    height: 987px;
  }
  .card {
    position: absolute;
    left: 292px;
    width: 616px;
    height: 352px;
    overflow: hidden;
    box-shadow: 0 3px 8px rgba(0,0,0,0.25);
  }
  .card-front {
    top: 130px;
    background: radial-gradient(ellipse 60% 75% at 72% 45%, var(--brand-blue) 0%, #0a2a9a 45%, var(--brand-navy) 100%);
  }
  .card-back {
    top: 505px;
    background: var(--paper);
  }
  .front-red-band {
    position: absolute;
    left: 0;
    top: 0;
    width: 66px;
    height: 100%;
    background: var(--brand-red);
  }
  .front-brand {
    position: absolute;
    left: 86px;
    top: 0;
    width: 250px;
    height: 100%;
    display: flex;
    align-items: center;
    justify-content: center;
  }
  .front-brand-name {
    margin: 0;
    color: var(--ink-light);
    font-weight: 700;
    font-size: 24px;
    line-height: 1.3;
    text-align: center;
  }
  .contact {
    position: absolute;
    right: 35px;
    top: 0;
    color: var(--ink-light);
    text-align: right;
  }
  .person-name {
    position: absolute;
    right: 0;
    top: 42px;
    margin: 0;
    white-space: nowrap;
    font-size: 21px;
    font-weight: 600;
    letter-spacing: 0.3px;
  }
  .person-role {
    position: absolute;
    right: 0;
    top: 70px;
    margin: 0;
    white-space: nowrap;
    font-size: 16px;
  }
  .address {
    position: absolute;
    right: 0;
    top: 146px;
    margin: 0;
    white-space: nowrap;
    font-size: 16px;
    line-height: 24px;
    font-style: normal;
  }
  .lines {
    position: absolute;
    right: 0;
    top: 202px;
    margin: 0;
    padding: 0;
    list-style: none;
    font-size: 16px;
    line-height: 23.5px;
  }
  .lines li {
    display: flex;
    justify-content: flex-end;
    align-items: center;
    gap: 6px;
    white-space: nowrap;
  }
  .lines svg {
    width: 15px;
    height: 15px;
    fill: var(--ink-light);
    flex: none;
  }
  .back-brand {
    position: absolute;
    inset: 0;
    display: flex;
    align-items: center;
    justify-content: center;
  }
  .back-brand-name {
    margin: 0;
    color: var(--wordmark-blue);
    font-weight: 700;
    font-size: 22px;
  }
</style>
</head>
<body>
<main class="canvas">

  <section class="card card-front" aria-label="Card front">
    <div class="front-red-band"></div>
    <div class="front-brand">
      <p class="front-brand-name">Harborline<br>Claims Advocates</p>
    </div>

    <div class="contact">
      <h1 class="person-name">DANIEL MARSH</h1>
      <p class="person-role">CEO/Founder</p>
      <address class="address">4120 Willow Crest Ave<br>Springfield, Illinois 60412</address>
      <ul class="lines">
        <li>312 555 0148
          <svg viewBox="0 0 16 16" aria-hidden="true"><path d="M3.6 1.2l2.3 2.6-1.2 1.8c.8 1.9 2.4 3.5 4.3 4.3l1.8-1.2 2.6 2.3-1.1 2.4C7 13.2 2.8 9 1.2 4.8z"/></svg>
        </li>
        <li>312 555 0193
          <svg viewBox="0 0 16 16" aria-hidden="true"><path d="M4.5 1h7v14h-7zM5.8 2.5v9.5h4.4V2.5zM7.4 13h1.2v1H7.4z" fill-rule="evenodd"/></svg>
        </li>
        <li>312 555 0177
          <svg viewBox="0 0 16 16" aria-hidden="true"><path d="M4 2h8v3H4zM1.5 6h13v6h-2.5V10H4v2H1.5zM5 11h6v3H5z"/></svg>
        </li>
        <li>hello@harborlineclaims.com
          <svg viewBox="0 0 16 16" aria-hidden="true"><path d="M1 3.5h14v9H1zM2.3 4.5 8 9l5.7-4.5z" fill-rule="evenodd"/></svg>
        </li>
        <li>www.harborlineclaims.com
          <svg viewBox="0 0 16 16" aria-hidden="true"><circle cx="8" cy="8" r="7"/><path d="M5 4c2 0 2 2 3.5 2.5S7 9 5.5 9 4 6 5 4zM10 10c1.5 0 2.5 1 2 2.5-1 .5-2.5 0-2.5-1z" fill="#0a1f80"/></svg>
        </li>
      </ul>
    </div>
  </section>

  <section class="card card-back" aria-label="Card back">
    <div class="back-brand">
      <p class="back-brand-name">Harborline Claims Advocates</p>
    </div>
  </section>

</main>
</body>
</html>
```